Stationary package for Interior and construction company
Silverleaf Habitat Interiors
Derek Fallowby
Project Manager
Warehouse K42, Dubai Industrial City Dubai,UAE PO Box 315604
silverleafhabitat@examplemail.com
www.silverleafhabitat-example.ae
We require two business cards with different peoples names. #1 been Derek Fallowby the second persons details are. Derek Winstanley, Project Manager, Warehouse K42, Dubai Industrial City, Dubai, UAE, PO Box 315604, Cell- +971 50 7718604 Ph- +971 4 3862157 Email - d.winstanley@silverleafinteriors-example.ae Web - www.silverleafinteriors-example.ae Brief, Silverleaf Habitat Interiors (SHI) is a luxury fit out and renovations company based in Dubai, UAE. SHI’s clientele are high net worth individuals. The company is looking for a suite of stationary to support their everyday business needs; this should include: • Letterheads (page 1 and page2) • Business cards (Two people) • Envelopes (A4, DL) • Notepad (A4, A5) The company would like to evoke a premium brand through chic, clean and sophisticated stationary items. Colour should not be over-used unnecessarily and the typeface should be clear to read. All artwork provided should be re-writable.
Please just use the logo, add the website to the bottom footer. open to options on layout and design.

```html
<!DOCTYPE html>
<html lang="en">
<head>
<meta charset="utf-8">
<title>Silverleaf Habitat Interiors – Business Card</title>
<link rel="stylesheet" href="https://fonts.googleapis.com/css2?family=Open+Sans:wght@400;600;700&display=swap">
<style>
  :root {
    --backdrop: #d9d9db;
    --card: #ffffff;
    --brand-blue: #2a9fd6;
    --brand-grey: #6d6e71;
    --ink: #3c3c3e;
    --on-blue: #ffffff;
  }
  * { box-sizing: border-box; margin: 0; padding: 0; }
  html, body {
    width: 1200px; height: 895px; overflow: hidden;
    background: var(--backdrop);
    font-family: "Open Sans", Arial, sans-serif;
    color: var(--ink);
  }
  .stage { position: relative; width: 1200px; height: 895px; }
  .card {
    position: absolute; width: 600px; height: 343px;
    background: var(--card);
    box-shadow: 0 6px 18px rgba(0,0,0,.18);
    overflow: hidden;
  }
  .card-back { left: 560px; top: 80px; }
  .card-front { left: 60px; top: 480px; }

  .brand-mark {
    display: inline-block; border-radius: 50%;
    background: var(--brand-blue);
  }
  .brand-name {
    color: var(--brand-grey); font-weight: 600;
    text-transform: uppercase; letter-spacing: 2px;
  }

  /* back */
  .web-band {
    position: absolute; left: 0; top: 44px;
    height: 34px; width: 300px;
    background: var(--brand-blue);
    border-radius: 0 17px 17px 0;
    color: var(--on-blue); font-size: 14px; letter-spacing: .5px;
    display: flex; align-items: center; padding-left: 24px;
  }
  .back-logo {
    position: absolute; left: 330px; top: 150px;
    display: flex; align-items: center; gap: 12px;
  }
  .back-logo .brand-mark { width: 56px; height: 56px; }
  .back-logo .brand-name { font-size: 15px; width: 190px; line-height: 1.3; }

  /* front */
  .front-logo {
    position: absolute; left: 36px; top: 38px;
    display: flex; align-items: center; gap: 16px;
  }
  .front-logo .brand-mark { width: 72px; height: 72px; }
  .front-logo .brand-name { font-size: 22px; line-height: 1.25; }
  .identity {
    position: absolute; left: 36px; top: 168px;
    font-size: 20px; display: flex; align-items: baseline; gap: 10px;
  }
  .identity .person { font-weight: 700; }
  .identity .divider { font-weight: 700; }
  .identity .role { font-size: 15px; }
  .address {
    position: absolute; left: 36px; top: 214px;
    font-size: 13px; display: flex; align-items: center; gap: 8px;
  }
  .contact-band {
    position: absolute; left: 0; top: 262px;
    height: 36px; width: 560px;
    background: var(--brand-blue);
    border-radius: 0 18px 18px 0;
    color: var(--on-blue); font-size: 12.5px;
    display: flex; align-items: center; gap: 16px; padding-left: 36px;
  }
  .contact-item { display: flex; align-items: center; gap: 6px; white-space: nowrap; }
  .icon { width: 14px; height: 14px; flex: none; }
</style>
</head>
<body>
<main class="stage">

  <section class="card card-back" aria-label="Business card back">
    <div class="web-band">www.silverleafhabitat-example.ae</div>
    <div class="back-logo">
      <span class="brand-mark"></span>
      <span class="brand-name">Silverleaf Habitat Interiors</span>
    </div>
  </section>

  <section class="card card-front" aria-label="Business card front">
    <div class="front-logo">
      <span class="brand-mark"></span>
      <span class="brand-name">Silverleaf Habitat<br>Interiors</span>
    </div>

    <p class="identity">
      <span class="person">Derek Fallowby</span>
      <span class="divider">|</span>
      <span class="role">Project Manager</span>
    </p>

    <p class="address">
      <svg class="icon" viewBox="0 0 14 14" aria-hidden="true">
        <path d="M7 1a4 4 0 0 1 4 4c0 3-4 8-4 8S3 8 3 5a4 4 0 0 1 4-4z" fill="#2a9fd6"/>
        <circle cx="7" cy="5" r="1.5" fill="#fff"/>
      </svg>
      Warehouse K42, Dubai Industrial City
    </p>

    <div class="contact-band">
      <span class="contact-item">
        <svg class="icon" viewBox="0 0 14 14" aria-hidden="true">
          <circle cx="7" cy="7" r="7" fill="#fff"/>
          <path d="M4.6 3.5l1.3 1.6-.7.9a5 5 0 0 0 2.8 2.8l.9-.7 1.6 1.3-.7 1.1C6.9 10.4 3.6 7.1 3.5 4.2z" fill="#2a9fd6"/>
        </svg>
        +971 50 7718604
      </span>
      <span class="contact-item">
        <svg class="icon" viewBox="0 0 14 14" aria-hidden="true">
          <circle cx="7" cy="7" r="7" fill="#fff"/>
          <path d="M4.6 3.5l1.3 1.6-.7.9a5 5 0 0 0 2.8 2.8l.9-.7 1.6 1.3-.7 1.1C6.9 10.4 3.6 7.1 3.5 4.2z" fill="#2a9fd6"/>
        </svg>
        +971 4 3862157
      </span>
      <span class="contact-item">
        <svg class="icon" viewBox="0 0 14 14" aria-hidden="true">
          <circle cx="7" cy="7" r="7" fill="#fff"/>
          <rect x="3.5" y="4.5" width="7" height="5" fill="none" stroke="#2a9fd6" stroke-width="1"/>
          <path d="M3.5 4.5L7 7.3l3.5-2.8" fill="none" stroke="#2a9fd6" stroke-width="1"/>
        </svg>
        silverleafhabitat@examplemail.com
      </span>
    </div>
  </section>

</main>
</body>
</html>
```